Stationery Design Project

Hi All,

We need you to design stationary for a new Business and Accounting Advisory Firm. We have already got the logo designed and it is attached. If you could also if possible, match the fonts in your design to that on the logo’s provided.

What we need:
- Business Card
- A4 Letter head
- A4 Folders
- PPT template (Title page and regular page)

And what ever else you want to throw in.

We are in the process of getting the web site designed, however below is a list of websites which we like which will give you an understanding of the style that we are going for.

- plivant.example
- moldrabay.example
- tarvenhook.example
- quillorbank.example

I look forward to your seeing your design.
Updates

Hi All,

I have just realised that I forgot that i need to include a Sworn Ledgerkeepers image on the letter head, please find attaced as File 1. Could you please have this image in the bottom left header.

Regards,

Marcus

Industry/Entity Type

Business

Requirements
Must have
• Outputs:
- Documents ready to print
- Generic editable information
- Pdf copies of the documents
- Word version of letterhead

```html
<!DOCTYPE html>
<html lang="en">
<head>
<meta charset="utf-8">
<title>Orvelmarsh Partners – Business Card Set</title>
<link rel="stylesheet" href="https://fonts.googleapis.com/css2?family=EB+Garamond:wght@500&family=Tinos:wght@400;700&display=swap">
<style>
  :root {
    --board: #8a8b8d;
    --paper: #ffffff;
    --ink: #222222;
    --brand-blue: #3a5a99;
    --brand-blue-light: #3fc0e0;
    --brand-orange: #f28226;
    --brand-yellow: #fcc934;
    --rule-grey: #9a9a9a;
  }
  * { margin: 0; padding: 0; box-sizing: border-box; }
  html, body {
    width: 1200px; height: 709px; overflow: hidden;
    background: var(--board);
  }
  .card-set { position: relative; width: 1200px; height: 709px; }
  .card {
    position: absolute; width: 558px; height: 318px;
    overflow: hidden; border: 1px solid #555;
  }
  .card--front { left: 25px; top: 26px; background: var(--paper); }
  .card--orange {
    left: 619px; top: 26px;
    background: radial-gradient(ellipse 55% 70% at 50% 48%, var(--brand-yellow) 0%, #f9a42c 45%, var(--brand-orange) 100%);
  }
  .card--blue {
    left: 25px; top: 365px;
    background: radial-gradient(ellipse 55% 65% at 50% 48%, var(--brand-blue-light) 0%, #3a88c0 40%, var(--brand-blue) 100%);
  }
  .card--white { left: 619px; top: 365px; background: var(--paper); }

  .brand {
    position: absolute; left: 0; right: 0;
    display: flex; align-items: center; justify-content: center; gap: 12px;
    font-family: "EB Garamond", Georgia, serif; font-weight: 500;
    white-space: nowrap;
  }
  .brand__mark { display: block; flex: none; }
  .brand--small { font-size: 30px; color: var(--brand-blue); }
  .brand--small .brand__mark { width: 40px; height: 40px; background: var(--brand-orange); }
  .brand--large { font-size: 50px; color: #ffffff; }
  .brand--large .brand__mark { width: 64px; height: 64px; border-radius: 50%; background: #ffffff; }

  .card--front .brand { top: 48px; }
  .card--orange .brand, .card--blue .brand { top: 108px; }
  .card--white .brand { top: 122px; }

  .web {
    position: absolute; left: 0; right: 0; text-align: center;
    font-family: Tinos, "Times New Roman", serif; font-size: 17px;
    letter-spacing: 2px; white-space: nowrap;
  }
  .card--orange .web, .card--blue .web { top: 268px; color: #ffffff; }
  .card--white .web { top: 240px; color: var(--ink); }

  .person {
    position: absolute; right: 300px; top: 166px; text-align: right;
    font-family: Tinos, "Times New Roman", serif; color: #333; font-size: 16px; line-height: 19px;
  }
  .person__name { font-weight: 700; font-size: 20px; color: var(--brand-blue); line-height: 24px; }
  .person__role { margin-bottom: 7px; }
  .divider {
    position: absolute; left: 273px; top: 158px; width: 1px; height: 95px; background: var(--rule-grey);
  }
  .contact {
    position: absolute; left: 288px; top: 174px; list-style: none;
    font-family: Tinos, "Times New Roman", serif; font-size: 16px; color: #333; line-height: 27px;
  }
  .contact li { display: flex; align-items: center; gap: 5px; white-space: nowrap; }
  .contact svg { width: 12px; height: 12px; fill: var(--brand-blue); flex: none; }

  .footer-rule { position: absolute; left: 0; right: 0; top: 287px; height: 2px; background: var(--brand-orange); }
  .footer-band {
    position: absolute; left: 0; right: 0; top: 290px; height: 28px;
    background: linear-gradient(180deg, #6fb0dd 0%, #3a7fbf 55%, #2f6aa8 100%);
  }
  .footer-band .web { top: 4px; color: #ffffff; font-size: 16px; letter-spacing: 2.5px; }
</style>
</head>
<body>
<main class="card-set">

  <section class="card card--front">
    <div class="brand brand--small"><span class="brand__mark"></span>Orvelmarsh Partners</div>

    <div class="person">
      <div class="person__name">Your Name</div>
      <div class="person__role">Designation</div>
      <div>Street Name, City Name</div>
      <div>State, City Zip Code</div>
    </div>
    <div class="divider"></div>
    <ul class="contact">
      <li><svg viewBox="0 0 12 12" aria-hidden="true"><path d="M3 1l2 2.5-1.2 1.2c.6 1.3 1.6 2.3 2.9 2.9L7.9 6.4 10.5 8.4 9.4 10.8C5 10.5 1.5 7 1.2 2.6z"/></svg>0123-456-789</li>
      <li><svg viewBox="0 0 12 12" aria-hidden="true"><path d="M2 6l1.5-3.5h5L10 6h1v3.5H9.8a1.2 1.2 0 0 1-2.4 0H4.6a1.2 1.2 0 0 1-2.4 0H1V6z"/></svg>0123-456-789</li>
      <li><svg viewBox="0 0 12 12" aria-hidden="true"><path d="M1 3h10v6.5H1z M1 3l5 4 5-4" fill="none" stroke="#3a5a99" stroke-width="1.4"/></svg>info@orvelmarshpartners.example</li>
    </ul>

    <div class="footer-rule"></div>
    <div class="footer-band"><div class="web">www.orvelmarshpartners.example</div></div>
  </section>

  <section class="card card--orange">
    <div class="brand brand--large"><span class="brand__mark"></span>Orvelmarsh Partners</div>
    <div class="web">www.orvelmarshpartners.example</div>
  </section>

  <section class="card card--blue">
    <div class="brand brand--large"><span class="brand__mark"></span>Orvelmarsh Partners</div>
    <div class="web">www.orvelmarshpartners.example</div>
  </section>

  <section class="card card--white">
    <div class="brand brand--small"><span class="brand__mark"></span>Orvelmarsh Partners</div>
    <div class="web">www.orvelmarshpartners.example</div>
  </section>

</main>
</body>
</html>
```